Business card

We need a business card design for our company based in Auckland , New Zealand called 'Ridge + Studio Ltd'. We provide architectural services. We would like to see designs that use the max. three colours (such as white, black, grey) The final design should communicate financial safety and growth."
Also I will provide our company logo. I would like to the logo to be embeded onto our business card.

Target Market(s)

new residential house, alteration & addition & light commericila design & drafting service

Industry/Entity Type

Architecture

Contact Information for Business Card

Company name: ridge + studio Ltd.
Name: Mark Delford
Job title: architectural designer & Design LBP
email address: mark@rplusd.co.nz
mobile number: 02 5163 2290
web site: www.rplusd.co.nz

Requirements
Must have
• My project must have..
• - embeded logo (attached company logo)
• I don't have a bigger version for our company logo, but I have one old one, so you can remove the word from it)
• - insert the attached small BKTW logo & LBP logo
• - creative, simple and clear business card.
• - Max. three colours
Nice to have
• - Here are the samples I would like to share with you: http://www.plimvora.com/blog/minimalistic-business-card-designs/
• I would like to have my business card like one of the creation.
Should not have
• TBA

```html
<!DOCTYPE html>
<html lang="en">
<head>
<meta charset="utf-8">
<title>Ridge + Studio Ltd — Business Card</title>
<link rel="stylesheet" href="https://fonts.googleapis.com/css2?family=Open+Sans:wght@400;600;700&display=swap">
<style>
  :root {
    --backdrop: #2b2b2d;
    --card-black: #1c1c1c;
    --ink-white: #f4f4f4;
    --ink-soft: #cfcfcf;
    --silver-light: #f1f1f1;
    --silver-mid: #d9d9d9;
    --graphite: #3a3a3a;
    --rule-grey: #8a8a8a;
  }
  * { box-sizing: border-box; margin: 0; padding: 0; }
  html, body {
    width: 1200px;
    height: 950px;
    overflow: hidden;
    background: var(--backdrop);
    font-family: "Open Sans", Arial, sans-serif;
  }
  .canvas {
    position: relative;
    width: 1200px;
    height: 950px;
  }
  .card {
    position: absolute;
    left: 270px;
    width: 660px;
    height: 400px;
    border-radius: 4px;
    box-shadow: 0 10px 28px rgba(0,0,0,0.45);
  }

  /* Front */
  .card--front {
    top: 45px;
    background: var(--card-black);
    color: var(--ink-white);
  }
  .brand {
    position: absolute;
    left: 56px;
    top: 180px;
    width: 260px;
    display: flex;
    align-items: center;
    gap: 12px;
  }
  .brand__dot {
    flex: none;
    width: 16px;
    height: 16px;
    border-radius: 50%;
    background: var(--ink-white);
  }
  .brand__name {
    font-size: 24px;
    font-weight: 600;
    letter-spacing: 0.5px;
    color: var(--ink-white);
    white-space: nowrap;
  }
  .contact {
    position: absolute;
    left: 360px;
    top: 98px;
  }
  .contact__name {
    font-size: 25px;
    font-weight: 600;
    letter-spacing: 0.5px;
    text-transform: uppercase;
    line-height: 1.2;
  }
  .contact__role {
    font-size: 18px;
    font-weight: 400;
    line-height: 1.3;
    color: var(--ink-soft);
    margin-top: 2px;
  }
  .contact__rule {
    width: 36px;
    height: 2px;
    background: var(--ink-soft);
    margin: 20px 0 18px;
  }
  .contact__company {
    font-size: 16px;
    font-weight: 700;
    margin-bottom: 8px;
  }
  .contact__line {
    font-size: 15px;
    line-height: 1.55;
    color: var(--ink-soft);
  }

  /* Back */
  .card--back {
    top: 495px;
    background: linear-gradient(135deg, var(--silver-light) 0%, var(--silver-mid) 100%);
    display: flex;
    align-items: center;
    justify-content: center;
    gap: 34px;
  }
  .partner-badge {
    width: 150px;
    height: 72px;
    background: var(--graphite);
    border-radius: 3px;
  }
  .badge-divider {
    width: 1px;
    height: 96px;
    background: var(--rule-grey);
  }
  .cert-badge {
    width: 118px;
    height: 118px;
    border-radius: 50%;
    background: var(--graphite);
  }
</style>
</head>
<body>
<main class="canvas">
  <section class="card card--front" aria-label="Business card front">
    <div class="brand">
      <span class="brand__dot" aria-hidden="true"></span>
      <span class="brand__name">ridge + studio</span>
    </div>
    <div class="contact">
      <h1 class="contact__name">Mark Delford</h1>
      <p class="contact__role">architectural designer &amp;<br>Design LBP</p>
      <div class="contact__rule"></div>
      <p class="contact__company">ridge + studio Ltd.</p>
      <p class="contact__line">02 5163 2290</p>
      <p class="contact__line">mark@rplusd.co.nz</p>
      <p class="contact__line">www.rplusd.co.nz</p>
    </div>
  </section>

  <section class="card card--back" aria-label="Business card back">
    <div class="partner-badge" role="img" aria-label="BKTW membership badge"></div>
    <div class="badge-divider"></div>
    <div class="cert-badge" role="img" aria-label="Licensed practitioner certification badge"></div>
  </section>
</main>
</body>
</html>
```